Modern Business Card

Modern professional business card with more than just logo and demographic info. Something memorable.

We are a trendy/modern chiropractic group with an emphasis on neurology, hence the minimalist-type brain logo. We want to convey that modern and technical aspect with professionalism and the elite nature of our practice environment.

```html
<!DOCTYPE html>
<html lang="en">
<head>
<meta charset="utf-8">
<title>Meridian Chiropractic – Business Card</title>
<link rel="stylesheet" href="https://fonts.googleapis.com/css2?family=Libre+Baskerville&family=Exo+2:wght@400;600&display=swap">
<style>
  :root {
    --stage: #1e1e1e;
    --card-dark: #0a0a0b;
    --card-dark-tone: #1c1d21;
    --card-dark-glow: #26272c;
    --card-light: #ffffff;
    --ink: #1a1a1a;
    --ink-soft: #555a60;
    --accent: #3f7fd0;
    --rule: #222;
  }
  * { box-sizing: border-box; margin: 0; padding: 0; }
  html, body { width: 1200px; height: 900px; overflow: hidden; }
  body {
    background: radial-gradient(ellipse at 60% 20%, #3a3a3a 0%, var(--stage) 55%, #0e0e0e 100%);
    position: relative;
  }
  .card {
    position: absolute;
    left: 290px;
    width: 620px;
    height: 354px;
    box-shadow: 0 18px 40px rgba(0,0,0,.55);
    overflow: hidden;
  }
  /* Back side */
  .card--back { top: 60px; background: var(--card-dark); }
  .card__texture {
    position: absolute; inset: 0;
    background:
      radial-gradient(ellipse 180px 90px at 15% 20%, var(--card-dark-glow), transparent 70%),
      radial-gradient(ellipse 200px 100px at 85% 25%, var(--card-dark-glow), transparent 70%),
      radial-gradient(ellipse 220px 110px at 50% 55%, var(--card-dark-tone), transparent 70%),
      radial-gradient(ellipse 180px 90px at 20% 85%, var(--card-dark-glow), transparent 70%),
      radial-gradient(ellipse 180px 90px at 82% 85%, var(--card-dark-glow), transparent 70%),
      linear-gradient(135deg, var(--card-dark-tone), var(--card-dark) 55%, var(--card-dark-tone));
  }
  .card__mark {
    position: absolute; left: 50%; top: 120px;
    width: 34px; height: 34px; margin-left: -17px;
    background: var(--accent);
  }
  .back-name {
    position: absolute; left: 0; right: 0; top: 236px;
    text-align: center; color: #fff;
    font-family: "Libre Baskerville", serif;
    line-height: 1;
  }
  .back-name__main { display: block; font-size: 30px; letter-spacing: 1px; }
  .back-name__sub { display: block; font-size: 13px; letter-spacing: 1.5px; margin-top: 3px; }

  /* Front side */
  .card--front { top: 486px; background: var(--card-light); }
  .brand {
    position: absolute; left: 36px; top: 140px;
    display: flex; align-items: center; gap: 14px;
    font-family: "Libre Baskerville", serif; color: var(--ink);
  }
  .brand__square { width: 36px; height: 36px; background: var(--accent); flex: none; }
  .brand__main { display: block; font-size: 34px; line-height: 1; }
  .brand__sub { display: block; font-size: 17px; letter-spacing: 1.5px; margin-top: 2px; }

  .person { position: absolute; left: 345px; top: 84px; width: 260px; }
  .person__name {
    font-family: "Libre Baskerville", serif; font-weight: 400;
    font-size: 22px; color: var(--ink-soft); letter-spacing: .5px;
  }
  .person__role {
    font-family: "Exo 2", sans-serif; font-size: 17px; color: var(--accent);
    margin-top: 2px;
  }
  .person__rule { width: 230px; height: 2px; background: var(--rule); margin: 10px 0 14px; }
  .contact { list-style: none; font-family: "Exo 2", sans-serif; font-size: 17px; color: var(--ink); }
  .contact li { display: flex; align-items: center; gap: 10px; margin-bottom: 6px; white-space: nowrap; }
  .contact svg { width: 18px; height: 18px; flex: none; stroke: var(--accent); fill: none; stroke-width: 1.6; }
  .contact__strong { color: var(--accent); font-weight: 600; }
</style>
</head>
<body>
  <section class="card card--back" aria-label="Card back">
    <div class="card__texture" role="img" aria-label="Faint repeating pattern of the practice symbol across a black surface"></div>
    <div class="card__mark"></div>
    <p class="back-name">
      <span class="back-name__main">MERIDIAN</span>
      <span class="back-name__sub">CHIROPRACTIC</span>
    </p>
  </section>

  <section class="card card--front" aria-label="Card front">
    <div class="brand">
      <span class="brand__square"></span>
      <p>
        <span class="brand__main">MERIDIAN</span>
        <span class="brand__sub">CHIROPRACTIC</span>
      </p>
    </div>

    <div class="person">
      <h1 class="person__name">OWEN CARTER</h1>
      <p class="person__role">Training Specialist</p>
      <div class="person__rule"></div>
      <ul class="contact">
        <li>
          <svg viewBox="0 0 20 20"><circle cx="10" cy="10" r="8.5"/><path d="M7 6.5c0 4 2.5 6.5 6.5 6.5l.8-1.6-1.8-1-1 .8c-1-.5-1.7-1.2-2.2-2.2l.8-1-1-1.8z"/></svg>
          555.014.2290
        </li>
        <li>
          <svg viewBox="0 0 20 20"><rect x="2" y="4.5" width="16" height="11"/><path d="M2 4.5l8 6 8-6"/></svg>
          o.carter@meridianchiro.com
        </li>
        <li>
          <svg viewBox="0 0 20 20"><circle cx="10" cy="10" r="8"/><ellipse cx="10" cy="10" rx="3.5" ry="8"/><path d="M2 10h16M3.5 6h13M3.5 14h13"/></svg>
          <span>www.<span class="contact__strong">meridianchiro</span>.com</span>
        </li>
      </ul>
    </div>
  </section>
</body>
</html>
```